Resposive web site in 4 languages + image gallery + logo design

We need a web page, which will work on all devices.
I have uploaded web page concept.
Company name: Praxelun
Industry/Entity Type
It Company
Logo Text
quality matters
Coding
Coded - Design and coding required
Number of Pages Required
1 page

```html
<!DOCTYPE html>
<html lang="en">
<head>
<meta charset="utf-8">
<title>Praxelun — Wood, Stone &amp; Restoration</title>
<link rel="stylesheet" href="https://fonts.googleapis.com/css2?family=Cinzel:wght@400;700&family=Lato:wght@400;700&family=Ubuntu:wght@500;700&display=swap">
<style>
:root{
  --orange:#f7941d;
  --navy:#1f4e79;
  --ink:#1c1c1c;
  --text:#3a3a3a;
  --grey-bg:#f1f1f1;
  --line:#c9c9c9;
  --white:#ffffff;
}
*{box-sizing:border-box;margin:0;padding:0}
html,body{width:1200px;height:2535px;overflow:hidden;background:var(--white)}
body{font-family:"Lato",sans-serif;color:var(--text);position:relative}
.topbar{height:37px;background:var(--orange);position:relative}
.topbar-tools{position:absolute;right:61px;top:0;display:flex;height:37px}
.tool{background:var(--navy);color:var(--white);font-weight:700;font-size:17px;display:flex;align-items:center;gap:10px;padding:0 22px}
.tool + .tool{border-left:2px solid #3d6a96}
.tool-square{width:24px;height:24px;background:var(--white);border-radius:3px}
.tool-dot{width:16px;height:16px;border-radius:50%;background:var(--white)}
.header{height:78px;position:relative;border-bottom:1px solid #e4e4e4}
.brand{position:absolute;left:61px;top:16px;font-family:"Cinzel",serif;font-weight:700;font-size:36px;color:var(--orange);letter-spacing:1px}
.nav{position:absolute;right:42px;top:0;display:flex;height:78px;align-items:center}
.nav a{font-family:"Cinzel",serif;font-size:18px;color:var(--ink);text-decoration:none;margin-left:56px;position:relative}
.nav a.active{color:var(--orange)}
.nav a.active::after{content:"";position:absolute;left:-6px;right:-6px;bottom:-9px;height:2px;background:var(--orange)}
.hero{height:490px;position:relative;background:linear-gradient(180deg,#c89a6a 0%,#e6cfae 28%,#dfe6ea 48%,#c7a784 72%,#a87a52 100%)}
.hero-title{position:absolute;top:336px;width:100%;text-align:center;font-family:"Ubuntu",sans-serif;font-weight:700;font-size:42px;color:var(--navy)}
.hero-cta{position:absolute;left:493px;top:408px;width:213px;height:44px;border-radius:22px;background:var(--orange);border:3px solid var(--navy);display:flex;align-items:center;color:var(--white);font-family:"Ubuntu",sans-serif;font-weight:500;font-size:22px}
.hero-cta .cta-icon{width:44px;height:44px;margin-left:-3px;border-radius:50%;background:var(--white);border:3px solid var(--navy);display:flex;align-items:center;justify-content:center;margin-right:12px}
.hero-arrow{position:absolute;top:340px}
.section-title{font-family:"Cinzel",serif;font-weight:700;font-size:36px;color:var(--ink);text-align:center;letter-spacing:1px}
.section-title span{color:var(--orange);font-weight:400}
.title-rule{width:535px;height:1px;background:var(--line);margin:12px auto 0;position:relative}
.title-rule::after{content:"";position:absolute;left:200px;width:135px;height:3px;top:-1px;background:var(--navy)}
.welcome{height:282px;padding-top:30px;text-align:center}
.welcome p{font-size:15px;line-height:25px;width:1070px;margin:22px auto 0}
.btn{display:inline-block;background:var(--navy);color:var(--white);font-size:14px;padding:8px 13px;border-radius:3px;margin-top:34px}
.services{background:var(--grey-bg);height:433px;position:relative;padding-top:34px}
.service{height:336px;position:relative}
.service.grey{background:var(--grey-bg);height:338px}
.service-media{position:absolute;width:287px;height:235px}
.thumbs{position:absolute;display:flex;flex-direction:column;gap:7px}
.thumb{width:54px;height:53px;border:2px solid var(--white);box-shadow:0 0 0 1px #cfcfcf}
.thumb.on{box-shadow:0 0 0 2px var(--orange)}
.service-title{position:absolute;font-family:"Lato",sans-serif;font-weight:400;font-size:27px;color:var(--navy)}
.service-text{position:absolute;font-size:15.5px;line-height:32px}
.quote-band{height:243px;background:linear-gradient(90deg,#1b4674,#24568a 50%,#1b4674);text-align:center;color:var(--white);padding-top:50px}
.quote-band p{font-size:19px;line-height:30px}
.quote-band .rule{width:450px;height:1px;background:#4d76a2;margin:18px auto 14px}
.quote-band strong{color:var(--orange);font-size:19px}
.footer{height:298px;position:relative}
.footer h4{font-family:"Cinzel",serif;font-weight:400;font-size:20px;color:var(--ink);letter-spacing:1px;padding-bottom:10px;border-bottom:2px solid var(--line)}
.col{position:absolute;top:38px}
.links li{list-style:none;font-size:14px;margin-top:22px;color:var(--ink)}
.links li::before{content:"›";color:var(--orange);margin-right:8px}
.links li.active{color:var(--orange);font-weight:700}
.contact-item{display:flex;gap:14px;font-size:14px;line-height:20px;margin-top:18px;color:var(--ink)}
.field{position:absolute;border:1px dashed #bdbdbd;font-size:13px;padding:6px 10px;color:var(--ink);background:var(--white)}
.submit{position:absolute;background:var(--orange);color:var(--white);font-weight:700;font-size:14px;padding:8px 15px;border-radius:2px}
.copyright{position:absolute;bottom:0;left:0;width:1200px;height:47px;background:var(--navy);color:var(--white);font-size:14px;text-align:center;line-height:47px}
</style>
</head>
<body>
<div class="topbar">
  <div class="topbar-tools">
    <div class="tool">Find Us On <span class="tool-square"></span></div>
    <div class="tool"><span class="tool-dot"></span>English
      <svg width="12" height="8" viewBox="0 0 12 8"><path d="M0 0h12L6 8z" fill="#fff"/></svg></div>
  </div>
</div>
<header class="header">
  <div class="brand">PRAXELUN</div>
  <nav class="nav">
    <a class="active">HOME</a><a>SERVICES</a><a>ABOUT US</a><a>CONTACT US</a>
  </nav>
</header>
<section class="hero" role="img" aria-label="Bright open-plan timber interior with wooden beams, columns and floor, city view through tall windows">
  <svg class="hero-arrow" style="left:38px" width="22" height="44" viewBox="0 0 22 44"><path d="M20 2 2 22l18 20" fill="none" stroke="#fff" stroke-width="2"/></svg>
  <svg class="hero-arrow" style="right:38px" width="22" height="44" viewBox="0 0 22 44"><path d="M2 2l18 20L2 42" fill="none" stroke="#fff" stroke-width="2"/></svg>
  <h1 class="hero-title">Are You Interested In An Estimate?</h1>
  <div class="hero-cta"><span class="cta-icon"><svg width="18" height="22" viewBox="0 0 18 22"><rect x="2" y="2" width="14" height="18" fill="none" stroke="#1f4e79" stroke-width="2"/><path d="M6 8h6M6 12h6M6 16h4" stroke="#1f4e79" stroke-width="2"/></svg></span>GET A QUOTE</div>
</section>
<section class="welcome">
  <h2 class="section-title">WELCOME TO <span>PRAXELUN</span></h2>
  <div class="title-rule"></div>
  <p>Praxelun is a company whose business operations include making wooden products, restoration and building structures from natural stone. All of our products are made by craftsmen and specialists who have extensive experience and knowledge in their fields. The products we offer are always handmade and we take the requests and ideas of the specific client into account We always strive to achieve the best possible quality.</p>
  <span class="btn">READ MORE</span>
</section>
<section class="services">
  <h2 class="section-title">OUR <span>SERVICES</span></h2>
  <div class="title-rule"></div>
  <div class="service-media" style="left:61px;top:141px;background:linear-gradient(160deg,#8a6f55,#c2a98a 55%,#3a302a)" role="img" aria-label="Wooden dining table with dark leather chairs"></div>
  <div class="thumbs" style="left:362px;top:141px">
    <div class="thumb" style="background:#9a6a44"></div><div class="thumb" style="background:#5a4a3c"></div><div class="thumb" style="background:#7d4f30"></div><div class="thumb" style="background:#c79a6e"></div>
  </div>
  <h3 class="service-title" style="left:463px;top:148px">WOOD WORKS</h3>
  <p class="service-text" style="left:463px;top:192px;width:680px">Timber is, in essence, a natural and warm material. Wood is also relatively durable and easy to work with, which has made it a favourite of builders throughout history. Our goal is to offer suitable products and quality furniture with installation and after-sales service to all of our clients. In order to achieve this, we' ready to help our clients in all stages of construction from design to production and maintenance</p>
</section>
<section class="service">
  <h3 class="service-title" style="left:61px;top:50px">STONE WORKS</h3>
  <p class="service-text" style="left:61px;top:94px;width:692px">The natural stone found in the ground has been used in construction for centuries because of its durability. A structure built by a skilled craftsman from natural stone is unique, genuine and durable, and perfect for our bracing climate. Our experienced craftsmen are ready to help you in all stages of construction from planning to completion.</p>
  <div class="service-media" style="left:781px;top:54px;background:linear-gradient(180deg,#9fa7a8,#8d8577 50%,#6f7a4e 80%,#5a5a5a)" role="img" aria-label="Stone house with natural stone garden wall and shrubs"></div>
  <div class="thumbs" style="left:1082px;top:54px">
    <div class="thumb" style="background:#9c9c98"></div><div class="thumb on" style="background:#8a8270"></div><div class="thumb" style="background:#6f7460"></div><div class="thumb" style="background:#3e3a34"></div>
  </div>
</section>
<section class="service grey">
  <div class="service-media" style="left:61px;top:53px;background:linear-gradient(180deg,#cfc6b4,#a08870 55%,#6e5742)" role="img" aria-label="Restored rustic dining room with wooden table and chandeliers"></div>
  <div class="thumbs" style="left:362px;top:53px">
    <div class="thumb" style="background:#a3864e"></div><div class="thumb" style="background:#8a5a3a"></div><div class="thumb" style="background:#6a6a6a"></div><div class="thumb" style="background:#c58a3c"></div>
  </div>
  <h3 class="service-title" style="left:463px;top:60px">RESTORATION</h3>
  <p class="service-text" style="left:463px;top:104px;width:680px">It's good to see that fixing old things has become popular again in recent years and people are trying to find ways to preserve valuable old windows and pieces of furniture before deciding to replace them. It is possible to give a new life to almost any wooden door,window, piece of furniture or staircase. The extensive experience of our craftsmen will help you achieve the desired result.</p>
</section>
<section class="quote-band">
  <p>All of our products are made by craftsmen and specialists who have extensive experience and knowledge in their fields.<br>The products we offer are always handmade and we take the requests and ideas of the specific client into account<br>We always strive to achieve the best possible quality.</p>
  <div class="rule"></div>
  <strong>QUALITY MATTERS, PRAXELUN</strong>
</section>
<footer class="footer">
  <div class="col" style="left:61px;width:148px">
    <h4>QUICK LINKS</h4>
    <ul class="links"><li class="active">Home</li><li>Services</li><li>About Us</li><li>Contact Us</li></ul>
  </div>
  <div class="col" style="left:285px;width:250px">
    <h4>CONTACT DETAILS</h4>
    <div class="contact-item"><svg width="16" height="22" viewBox="0 0 16 22"><path d="M8 0a8 8 0 0 0-8 8c0 6 8 14 8 14s8-8 8-14a8 8 0 0 0-8-8z" fill="#f7941d"/><circle cx="8" cy="8" r="3" fill="#fff"/></svg><div><b>PRAXELUN</b><br>Vaskra 12, 10417 Norvall<br>Estland</div></div>
    <div class="contact-item"><svg width="16" height="16" viewBox="0 0 16 16"><path d="M3 1l3 3-2 2c1 2 4 5 6 6l2-2 3 3-2 2C7 15 1 9 1 3z" fill="#f7941d"/></svg>555-014-2287</div>
    <div class="contact-item"><svg width="16" height="12" viewBox="0 0 16 12"><rect width="16" height="12" fill="#f7941d"/><path d="M1 1l7 6 7-6" fill="none" stroke="#fff" stroke-width="1.5"/></svg>sales@praxelun.com</div>
  </div>
  <div class="col" style="left:610px;width:530px">
    <h4>QUICK INQUIRY</h4>
  </div>
  <div class="field" style="left:614px;top:91px;width:250px;height:32px">Name</div>
  <div class="field" style="left:614px;top:139px;width:250px;height:32px">Phone</div>
  <div class="field" style="left:614px;top:187px;width:250px;height:32px">Email</div>
  <div class="field" style="left:878px;top:91px;width:262px;height:80px">Message</div>
  <div class="submit" style="left:878px;top:187px">SUBMIT</div>
  <div class="copyright">COPYRIGHT © 2016 PRAXELUN. ALL RIGHTS RESERVED.</div>
</footer>
</body>
</html>
```